RESIDENTIAL CONSTRUCTION

We are a company that specializes in building custom residential homes, the design should also emphasize that quality and service is our priority.

Industry/Entity Type

Construction Company

Contact Information for Business Card

Contact Person: Marcus Lindqvist
Company Address: 273 West Alder Ave San Jose , Ca 95380
Phone Number : 408-731-2946
Email Address: Stoneridgehomes517@mailvista.net

Font styles to use
Sans Serif

Colors
ec1f27

Requirements
Must have
• CSLB # 7362015
Nice to have
• needs to have same color as logo i uploaded, we will be printing these on a clear plastic card.

```html
<!DOCTYPE html>
<html lang="en">
<head>
<meta charset="UTF-8">
<title>Stoneridge Homes – Business Card</title>
<link rel="stylesheet" href="https://fonts.googleapis.com/css2?family=Oswald:wght@500&family=Lato:wght@400&display=swap">
<style>
  :root {
    --page-bg: #e9e7e4;
    --card-black: #000000;
    --brand-red: #ec1f27;
    --accent-red: #c41e32;
    --text-light: #f2f2f2;
    --saw-tone: #ecebe8;
  }
  html, body {
    margin: 0;
    width: 1200px;
    height: 900px;
    overflow: hidden;
    background: var(--page-bg);
  }
  .business-card {
    position: absolute;
    left: 150px;
    top: 172px;
    width: 900px;
    height: 556px;
    background: var(--card-black);
    overflow: hidden;
    box-shadow: 0 10px 30px rgba(0,0,0,0.25);
  }
  .card-art {
    position: absolute;
    inset: 0;
  }
  .brand {
    position: absolute;
    left: 36px;
    top: 92px;
    display: flex;
    align-items: center;
    gap: 14px;
  }
  .brand-square {
    width: 34px;
    height: 34px;
    background: var(--brand-red);
  }
  .brand-name {
    font-family: "Oswald", sans-serif;
    font-weight: 500;
    font-size: 48px;
    line-height: 1;
    letter-spacing: 0.5px;
    color: var(--brand-red);
    text-transform: uppercase;
  }
  .contact-name {
    position: absolute;
    left: 36px;
    top: 270px;
    margin: 0;
    font-family: "Oswald", sans-serif;
    font-weight: 500;
    font-size: 32px;
    color: var(--accent-red);
    text-transform: uppercase;
  }
  .details {
    font-family: "Lato", sans-serif;
    font-size: 24px;
    color: var(--text-light);
    line-height: 1.35;
  }
  .address {
    position: absolute;
    left: 40px;
    top: 336px;
    margin: 0;
    font-style: normal;
  }
  .contact-lines {
    position: absolute;
    left: 36px;
    top: 424px;
    margin: 0;
    padding: 0;
    list-style: none;
  }
  .contact-lines li {
    display: flex;
    align-items: center;
    gap: 8px;
  }
  .contact-icon {
    width: 20px;
    height: 20px;
    flex: none;
  }
  .license {
    position: absolute;
    left: 522px;
    top: 462px;
    margin: 0;
  }
</style>
</head>
<body>
  <div class="business-card">
    <svg class="card-art" width="900" height="556" viewBox="0 0 900 556">
      <polygon class="red-band" points="660,0 900,0 900,556 806,556" fill="var(--accent-red)"/>
      <polygon class="saw-illustration" role="img" aria-label="Hand saw illustration running diagonally down the card"
               points="548,66 652,0 690,0 806,556 768,556" fill="var(--saw-tone)"/>
    </svg>

    <div class="brand">
      <span class="brand-square"></span>
      <span class="brand-name">Stoneridge Homes</span>
    </div>

    <h1 class="contact-name">Marcus Lindqvist</h1>

    <address class="address details">
      273 West Alder Ave San Jose<br>
      Ca 95380
    </address>

    <ul class="contact-lines details">
      <li>
        <svg class="contact-icon" viewBox="0 0 20 20" aria-hidden="true">
          <path d="M3 7c0-2 3-4 7-4s7 2 7 4v2h-4V7H7v2H3z M5 10h10l2 7H3z" fill="var(--accent-red)"/>
          <circle cx="10" cy="13.5" r="2" fill="var(--card-black)"/>
        </svg>
        408-731-2946
      </li>
      <li>
        <svg class="contact-icon" viewBox="0 0 20 20" aria-hidden="true">
          <rect x="1" y="4" width="18" height="12" fill="var(--accent-red)"/>
          <polyline points="1,4 10,11 19,4" fill="none" stroke="var(--card-black)" stroke-width="1.5"/>
        </svg>
        Stoneridgehomes517@mailvista.net
      </li>
    </ul>

    <p class="license details">CSLB # 7362015</p>
  </div>
</body>
</html>
```